Business Card Design for Software Development Company

I am looking for a business card design the incorporates my new logo (attached below).

Key information to include:
Name: Martin Quelbrook
Title: CEO
Email: martin@brightwellcivic.example
Phone: 555-218-9403
Website: www.brightwellcivic.example

NOTE: This design should be easy to edit so that we can order cards for different members of our team.

```html
<!DOCTYPE html>
<html lang="en">
<head>
<meta charset="utf-8">
<title>Brightwell Labs – Business Card</title>
<link href="https://fonts.googleapis.com/css2?family=Montserrat:wght@400;500;600&display=swap" rel="stylesheet">
<style>
  :root {
    --backdrop: #9b9b9b;
    --card: #f8f8f6;
    --ink: #2f3549;
    --ink-soft: #4a5064;
    --rule: #5a6075;
    --accent: #1fa88f;
  }
  * { box-sizing: border-box; margin: 0; padding: 0; }
  html, body {
    width: 1200px; height: 956px; overflow: hidden;
    background: var(--backdrop);
    font-family: "Montserrat", sans-serif;
    color: var(--ink);
  }
  .sheet {
    width: 1200px; height: 956px;
    display: flex; flex-direction: column; align-items: center; justify-content: center;
    gap: 54px;
  }
  .card {
    position: relative;
    width: 600px; height: 343px;
    background: var(--card);
    box-shadow: 0 14px 34px rgba(0,0,0,0.22);
  }
  .brand {
    position: absolute;
    display: flex; flex-direction: column; align-items: flex-end;
  }
  .brand-row { display: flex; align-items: center; gap: 12px; }
  .brand-mark { width: 26px; height: 26px; background: var(--accent); }
  .brand-name {
    font-weight: 600; font-size: 46px; letter-spacing: -0.5px; line-height: 1;
    color: var(--ink);
  }
  .brand-tagline {
    margin-top: 6px;
    font-size: 7.5px; font-weight: 500; letter-spacing: 1.2px; text-transform: uppercase;
    color: var(--ink);
  }
  .card-front .brand { top: 72px; right: 70px; }
  .card-back .brand { top: 130px; left: 50%; transform: translateX(-50%); }

  .person {
    position: absolute; left: 40px; top: 210px; width: 250px;
    text-align: right;
  }
  .person-name {
    font-size: 20px; font-weight: 500; letter-spacing: 1px; text-transform: uppercase;
  }
  .person-title { font-size: 15px; color: var(--ink-soft); margin-top: 2px; }
  .divider {
    position: absolute; left: 308px; top: 208px;
    width: 1px; height: 86px; background: var(--rule);
  }
  .contact {
    position: absolute; left: 326px; top: 208px;
    list-style: none; font-size: 13.5px; color: var(--ink);
  }
  .contact li { display: flex; align-items: center; gap: 9px; height: 28px; }
  .contact svg { width: 12px; height: 12px; flex: none; fill: var(--ink-soft); }
</style>
</head>
<body>
<main class="sheet">
  <section class="card card-front">
    <div class="brand">
      <div class="brand-row">
        <span class="brand-mark"></span>
        <span class="brand-name">Brightwell Labs</span>
      </div>
      <span class="brand-tagline">A division of Brightwell Civic</span>
    </div>

    <div class="person">
      <p class="person-name">Martin Quelbrook</p>
      <p class="person-title">CEO</p>
    </div>
    <div class="divider"></div>
    <ul class="contact">
      <li>
        <svg viewBox="0 0 24 24" aria-hidden="true"><path d="M6.6 10.8a15 15 0 0 0 6.6 6.6l2.2-2.2c.3-.3.7-.4 1-.2 1.1.4 2.3.6 3.6.6.6 0 1 .4 1 1V20c0 .6-.4 1-1 1A17 17 0 0 1 3 4c0-.6.4-1 1-1h3.5c.6 0 1 .4 1 1 0 1.3.2 2.5.6 3.6.1.3 0 .7-.2 1z"/></svg>
        555-218-9403
      </li>
      <li>
        <svg viewBox="0 0 24 24" aria-hidden="true"><path d="M2 5h20v14H2z M2 5l10 8 10-8" fill="none" stroke="#4a5064" stroke-width="2"/></svg>
        martin@brightwellcivic.example
      </li>
      <li>
        <svg viewBox="0 0 24 24" aria-hidden="true"><g fill="none" stroke="#4a5064" stroke-width="2"><circle cx="12" cy="12" r="10"/><ellipse cx="12" cy="12" rx="4.5" ry="10"/><path d="M2 12h20M4 7h16M4 17h16"/></g></svg>
        www.brightwellcivic.example
      </li>
    </ul>
  </section>

  <section class="card card-back">
    <div class="brand">
      <div class="brand-row">
        <span class="brand-mark"></span>
        <span class="brand-name">Brightwell Labs</span>
      </div>
      <span class="brand-tagline">A division of Brightwell Civic</span>
    </div>
  </section>
</main>
</body>
</html>
```